Upscale business cards needed for Board of Directors

We need professional business cards created for members of our family business Board of Directors. We would like these relatively simple and straightforward, but also with a unique element to set them apart. Probably stick with neutral and simple colors - white, grey etc. We need space for the traditional elements, including name, title, address, email/phone number. And we will be creating several from this template so it needs to be template that is easy to switch information in and out of.
Business
See description

```html
<!DOCTYPE html>
<html lang="en">
<head>
<meta charset="utf-8">
<title>Kestrel Holdings — Business Card</title>
<link rel="stylesheet" href="https://fonts.googleapis.com/css2?family=Roboto:wght@400;700&display=swap">
<style>
  :root {
    --backdrop: #2e2f31;
    --card-black: #151314;
    --card-white: #ffffff;
    --gold: #b49e73;
    --ink: #2a2a2a;
    --ink-soft: #4a4a4a;
    --paper-text: #f4f4f4;
  }
  * { margin: 0; padding: 0; box-sizing: border-box; }
  html, body {
    width: 1200px;
    height: 843px;
    overflow: hidden;
    background: var(--backdrop);
    font-family: "Roboto", Arial, sans-serif;
  }
  .stage {
    position: relative;
    width: 1200px;
    height: 843px;
  }
  .card {
    position: absolute;
    top: 278px;
    width: 500px;
    height: 286px;
    border-radius: 3px;
    box-shadow: 0 10px 24px rgba(0,0,0,0.45);
    overflow: hidden;
  }
  /* Back side */
  .card--back {
    left: 70px;
    background: var(--card-black);
    display: flex;
    flex-direction: column;
    align-items: center;
    justify-content: center;
  }
  .brand {
    font-weight: 700;
    text-transform: uppercase;
    line-height: 1;
    text-align: center;
  }
  .brand__name {
    display: block;
    font-size: 44px;
    letter-spacing: 1px;
  }
  .brand__sub {
    display: block;
    font-size: 17px;
    letter-spacing: 9px;
    margin-top: 4px;
    padding-left: 9px;
  }
  .card--back .brand { color: var(--paper-text); }
  .card--back .web {
    margin-top: 34px;
    color: var(--paper-text);
    font-size: 11px;
    letter-spacing: 3px;
  }
  /* Front side */
  .card--front {
    left: 630px;
    background: var(--card-white);
  }
  .name-band {
    position: absolute;
    top: 0;
    right: 40px;
    width: 190px;
    height: 118px;
    background: var(--gold);
    color: var(--card-white);
    padding: 0 16px 14px;
    display: flex;
    flex-direction: column;
    justify-content: flex-end;
  }
  .name-band__name {
    font-size: 17px;
    font-weight: 400;
    letter-spacing: 0.5px;
    text-transform: uppercase;
  }
  .name-band__title {
    font-size: 12px;
    margin-top: 3px;
  }
  .front-info {
    position: absolute;
    right: 40px;
    top: 140px;
    text-align: right;
  }
  .card--front .brand {
    color: var(--ink);
    text-align: right;
  }
  .card--front .brand__name { font-size: 34px; }
  .card--front .brand__sub { font-size: 13px; letter-spacing: 7px; padding-left: 0; margin-right: -7px; }
  .contact {
    margin-top: 16px;
    font-size: 10.5px;
    line-height: 1.45;
    color: var(--ink-soft);
    list-style: none;
  }
  .contact b { font-weight: 700; color: var(--ink); }
</style>
</head>
<body>
<main class="stage">
  <section class="card card--back" aria-label="Card back">
    <div class="brand">
      <span class="brand__name">Kestrel</span>
      <span class="brand__sub">Holdings</span>
    </div>
    <p class="web">www.example.com</p>
  </section>

  <section class="card card--front" aria-label="Card front">
    <div class="name-band">
      <p class="name-band__name">Marcus Hale</p>
      <p class="name-band__title">President</p>
    </div>
    <div class="front-info">
      <div class="brand">
        <span class="brand__name">Kestrel</span>
        <span class="brand__sub">Holdings</span>
      </div>
      <ul class="contact">
        <li>4127 Linden Crest Road</li>
        <li>Cedar Grove, NY 11420</li>
        <li><b>P :</b> 555 0142 7780</li>
        <li><b>E :</b> marcus@example.com</li>
        <li><b>W :</b> www.example.com</li>
      </ul>
    </div>
  </section>
</main>
</body>
</html>
```